Verodex business card

Business card for sustainable investment company called "Verodex". Verodex is an exchange platform selling carbon credits between buyers and sellers. Carbon Credits are an environmental commodity for reducing global carbon emissions.

the card should obviously have our logo and the theme should be sustainability/environment mixed with a trading platform.

Contact Information for Business Card

Logo, Name, Title, Phone, Email

Colors
0054AA
0677BA
7BADD7
CADEEF
E8F1F8
0094D4
00A9DD
6FCCEA
C7EBF8
E9F6FB
00AB8E
00BBA5
67D7C9
C6EFE9
E9F9F6
59FF00
82FF00
B8FF75
E3FFCB
F4FFEA

```html
<!DOCTYPE html>
<html lang="en">
<head>
<meta charset="utf-8">
<title>Verodex business card</title>
<link href="https://fonts.googleapis.com/css2?family=Figtree:wght@400;500;600;700&display=swap" rel="stylesheet">
<style>
  :root {
    --backdrop: #e6e7e9;
    --paper: #f4f4f5;
    --emboss: #e3e3e6;
    --navy: #050d33;
    --ink: #0d1a45;
    --teal: #1fa8c9;
    --blue: #0054aa;
    --mid-blue: #0677ba;
    --wordmark: #e4e6ee;
  }
  * { box-sizing: border-box; margin: 0; padding: 0; }
  html, body {
    width: 1200px; height: 1200px; overflow: hidden;
    background: var(--backdrop);
    font-family: "Figtree", Arial, sans-serif;
  }
  .card {
    position: absolute; left: 209px; width: 796px; height: 441px; overflow: hidden;
  }
  .card--front { top: 98px; background: var(--paper); }
  .card--back { top: 634px; background: var(--navy); }

  .emboss-name {
    position: absolute; left: 0; right: 0; top: -18px;
    text-align: center;
    font-size: 152px; font-weight: 600; letter-spacing: 2px;
    color: var(--emboss); line-height: 1;
  }

  .person {
    position: absolute; right: 491px; top: 232px; text-align: right;
  }
  .person__name {
    font-size: 36px; font-weight: 700; line-height: 1;
    background: linear-gradient(90deg, var(--teal), var(--blue));
    -webkit-background-clip: text; background-clip: text; color: transparent;
  }
  .person__title {
    margin-top: 10px; font-size: 22px; font-weight: 500; color: var(--ink);
  }

  .divider {
    position: absolute; left: 343px; top: 199px; width: 2px; height: 140px;
    background: linear-gradient(180deg, var(--teal), var(--blue));
  }

  .contact {
    position: absolute; left: 387px; top: 193px; color: var(--ink);
    font-size: 21px; font-weight: 500; line-height: 1.3;
  }
  .contact__office { font-weight: 700; }
  .contact__list { list-style: none; margin-top: 10px; }
  .contact__item { display: flex; align-items: center; gap: 8px; height: 29px; }
  .contact__icon { width: 17px; height: 17px; flex: none; }

  .brand {
    position: absolute; left: 150px; top: 190px;
    display: flex; align-items: center; gap: 28px;
  }
  .brand__dot {
    width: 62px; height: 62px; border-radius: 50%; background: var(--mid-blue);
  }
  .brand__name {
    font-size: 64px; font-weight: 700; color: var(--wordmark);
    letter-spacing: 1px; line-height: 1;
  }
</style>
</head>
<body>

<section class="card card--front">
  <div class="emboss-name" aria-hidden="true">VERODEX</div>

  <div class="person">
    <p class="person__name">Mark Halden</p>
    <p class="person__title">Sales Representative</p>
  </div>

  <div class="divider"></div>

  <div class="contact">
    <p class="contact__office">Verodex Head Office</p>
    <p class="contact__address">Budapest XIII. Tavasz utca 12.</p>
    <ul class="contact__list">
      <li class="contact__item">
        <svg class="contact__icon" viewBox="0 0 24 24" aria-hidden="true"><path fill="#0677BA" d="M6.6 10.8a15 15 0 0 0 6.6 6.6l2.2-2.2c.3-.3.7-.4 1-.2 1.1.4 2.3.6 3.6.6.6 0 1 .4 1 1V20c0 .6-.4 1-1 1A17 17 0 0 1 3 4c0-.6.4-1 1-1h3.5c.6 0 1 .4 1 1 0 1.3.2 2.5.6 3.6.1.3 0 .7-.2 1z"/></svg>
        <span>+36 30 555 0142</span>
      </li>
      <li class="contact__item">
        <svg class="contact__icon" viewBox="0 0 24 24" aria-hidden="true"><rect x="2" y="5" width="20" height="14" rx="1.5" fill="#0677BA"/><path d="M3 6l9 7 9-7" fill="none" stroke="#f4f4f5" stroke-width="1.6"/></svg>
        <span>szerviz@verodex.com</span>
      </li>
      <li class="contact__item">
        <svg class="contact__icon" viewBox="0 0 24 24" aria-hidden="true"><g fill="none" stroke="#0677BA" stroke-width="2"><circle cx="12" cy="12" r="9"/><ellipse cx="12" cy="12" rx="4" ry="9"/><path d="M3 12h18"/></g></svg>
        <span>www.verodex.com</span>
      </li>
    </ul>
  </div>
</section>

<section class="card card--back">
  <div class="brand">
    <span class="brand__dot"></span>
    <span class="brand__name">VERODEX</span>
  </div>
</section>

</body>
</html>
```